physio rehab flyer for Vela Mend please

Specification:
Flyer is to be trifold from letter size (8.5 x 11)
-----------------------This may help you:--------------------------
I would like the look of :
clean, minimalistic look with mainly blue and green
san serif font
professional
The colors I like are blue (not the blue in the logo enclosed, I want a change, but more like the blue on my website logo) and light green.
This is my website: www.velamendgroup.ca just so you get an idea but it will be totally changed soon to a to be determined design.
I like the blue and green in file "sample 2" (enclosed)
I like the pictures in "sample 2" file enclosed
For inspiration, I like design of this brochure: http://www.brelford.ca/HarlowRehab/PatientsFamilies/Clinics_Tests/DKAP_Service/Documents/Brochure.pdf
Here's how I see the pages layout:
----[location: this should be the cover (outside, right panel of trifold)]-----
Vela Mend Logo
Integrated Injury Rehab
Evidence-based, one-on-one care to make your recovery fast and comfortable
www.velamendgroup.ca
---------------[location: inside, left panel]----------------------------------------
Our team leaders
[portrait here]
Harriet Olsavik, MD, FRCPC, MSC, CIME
Physiatrist
Dr. Olsavik specializes in injury rehab and sports medicine. She is highly trained having received her MD and Residency in Physiatry from Pellham Institute. Her passion is to help injured people get back to their life.
[portrait here]
Wendy Carstairs, PT
Physiotherapist
Wendy has over 10 years of experience as a Physiotherapist (5 in Canada). She has advanced training in orthopedics and manual therapy. She loves and relates well with people from the youngest to the most senior.
--------------------[location: inside, middle panel]-------------------------------
Our services
We provide integrated assessment and care from interprofessional team of regulated healthcare professionals with proven experience in injury rehabilitation:
physiatrists
sport medicine physicians
physiotherapists
chiropractors
massage therapists
acupuncturists
psychologists
We provide custom medical bracing, orthotics, orthopedic shoes, assistive devices, and medical stockings, all in one place.
----------------------[location: inside, right panel]-----------------------------------
Only registered physiotherapists
We strongly believe in consistency with your treatment plan. This means that you spend your time here one-on-one with your physiotherapist, not any students or assistants. You get consistent high quality care from a professional.
One-on-one attention
We book maximum 3 people per hour to ensure everyone gets adequate one-on-one time with their physiotherapist. This compares favorably with other clinics, who may book upwards of 5-6 per hour. The atmosphere is professional -balanced with friendly, caring and relaxed. Our highly qualified staff operate this way to help make your recovery faster and more enjoyable.
------------------------[location: outside, left panel]---------------------------------
The right rehab for your clients
Timely access to comprehensive assessment and treatment
Proven track record in injury rehabilitation
Convenient one-stop service
Customized treatment plans
Integrated, co-ordinated care
Evidence-based care applying leading best practices
Access to specialty clinics: Physiatry and Chronic Pain
-------------------------[location: outside, middle panel]--------------------------
Please call us 555-384-2096
for more information on injury rehabilitation
Vela Mend Group
1862 Wexmoor Rd., Unit 9
Scarborough, ON K4T 8B2
[Please include a line art map designed based on "map" file enclosed]
To make a referral for your clients, contact velamendgroup@corvamail.ca or fax: 555-384-2071. Thank you.
www.velamendgroup.ca
------------------------------------------------------------------------------------------------
Target Market(s)
family doctors, ER docs, lawyers, and general public age (20-50)
Industry/Entity Type
Health And Wellness
Requirements
Must have
- san serif font
- blue and green colors
- clean, sophisticated look
Nice to have
- consumer choice award badge either on front or back of trifold
- see above

```html
<!DOCTYPE html>
<html lang="en">
<head>
<meta charset="utf-8">
<title>Vela Mend Group – Inside Spread</title>
<link href="https://fonts.googleapis.com/css2?family=Source+Sans+3:wght@400;600;700&display=swap" rel="stylesheet">
<style>
  :root {
    --blue: #5a86c5;
    --blue-deep: #4a7cc0;
    --blue-title: #4d80c2;
    --green: #c6dc62;
    --ink: #444a50;
    --white: #ffffff;
    --text-on-blue: #f1f5fb;
    --fold: #3f5f8f;
  }
  * { box-sizing: border-box; margin: 0; padding: 0; }
  html, body { width: 1200px; height: 928px; overflow: hidden; background: var(--white); }
  body { font-family: "Source Sans 3", "Myriad Pro", Arial, sans-serif; color: var(--ink); }
  .spread { position: relative; width: 1200px; height: 928px; overflow: hidden; background: var(--white); }

  /* left panel */
  .team { position: absolute; left: 0; top: 0; width: 400px; height: 928px; border-right: 1px solid #c8ccd2; }
  .team-title { position: absolute; left: 83px; top: 59px; font-size: 29px; line-height: 38px; font-weight: 700; color: var(--blue-title); }
  .leader-band { position: absolute; left: 0; width: 400px; height: 84px; }
  .leader-band.is-blue { top: 182px; background: var(--blue); }
  .leader-band.is-green { top: 528px; background: var(--green); }
  .portrait { position: absolute; left: 35px; width: 123px; height: 148px; border-radius: 14px 0 14px 0; }
  .portrait.is-first { top: 140px; background: linear-gradient(160deg, #cfc3b4, #e8e2da 55%, #f6f5f3); border-left: 5px solid var(--green); border-top: 5px solid var(--green); }
  .portrait.is-second { top: 505px; width: 120px; background: linear-gradient(160deg, #d8dfe6, #efe4df 55%, #f4f1f0); border-left: 5px solid var(--blue); border-top: 5px solid var(--blue); }
  .leader-name { position: absolute; left: 172px; color: var(--white); font-size: 15.5px; line-height: 19.5px; }
  .leader-name strong { font-weight: 700; font-size: 17px; }
  .leader-name.is-first { top: 194px; }
  .leader-name.is-second { top: 549px; }
  .leader-bio { position: absolute; left: 35px; width: 330px; font-size: 15.2px; line-height: 24.6px; text-align: justify; color: var(--ink); }
  .leader-bio.is-first { top: 306px; }
  .leader-bio.is-second { top: 671px; }
  .site-url { position: absolute; left: 60px; top: 858px; font-size: 22px; line-height: 30px; font-weight: 700; color: var(--blue-deep); }

  /* inside middle + right */
  .backdrop { position: absolute; left: 400px; top: 0; width: 800px; height: 928px; }
  .fold { position: absolute; left: 798px; top: 0; width: 1px; height: 928px; background: var(--fold); opacity: .7; }

  .panel-heading { position: absolute; font-size: 20px; font-weight: 700; color: var(--white); line-height: 25px; }
  .panel-text { position: absolute; font-size: 15.2px; line-height: 24.6px; color: var(--text-on-blue); }

  .services-title { left: 443px; top: 522px; }
  .services-intro { left: 443px; top: 554px; width: 318px; }
  .service-list { position: absolute; left: 443px; top: 660px; list-style: none; color: var(--white); }
  .service-list li { font-size: 15.2px; font-weight: 700; line-height: 20.6px; padding-left: 11px; position: relative; }
  .service-list li::before { content: ""; position: absolute; left: 0; top: 8px; width: 5px; height: 5px; border-radius: 50%; background: var(--green); }
  .services-extra { left: 443px; top: 812px; width: 318px; }

  .registered-title { left: 842px; top: 447px; width: 316px; text-align: right; }
  .registered-text { left: 842px; top: 519px; width: 316px; text-align: justify; }
  .attention-title { left: 842px; top: 651px; }
  .attention-text { left: 842px; top: 691px; width: 316px; text-align: justify; }
</style>
</head>
<body>
<div class="spread">

  <section class="team">
    <h2 class="team-title">Our team leaders</h2>

    <div class="leader-band is-blue"></div>
    <div class="portrait is-first" role="img" aria-label="Portrait of Dr. Harriet Olsavik in a white coat"></div>
    <p class="leader-name is-first"><strong>Harriet Olsavik,</strong><br>MD, FRCPC, MSC, CIME<br>Physiatrist</p>
    <p class="leader-bio is-first">Dr. Olsavik specializes in injury rehab and sports medicine. She is highly trained having received her MD and Residency in Physiatry from Pellham Institute. Her passion is to help injured people get back to their life.</p>

    <div class="leader-band is-green"></div>
    <div class="portrait is-second" role="img" aria-label="Portrait of physiotherapist Wendy Carstairs"></div>
    <p class="leader-name is-second"><strong>Wendy Carstairs, PT</strong><br>Physiotherapist</p>
    <p class="leader-bio is-second">Wendy has over 10 years of experience as a Physiotherapist (5 in Canada). She has advanced training in orthopedics and manual therapy. She loves and relates well with people from the youngest to the most senior.</p>

    <p class="site-url">www.velamendgroup.ca</p>
  </section>

  <svg class="backdrop" width="800" height="928" viewBox="0 0 800 928">
    <defs>
      <linearGradient id="photoTone" x1="0" y1="0" x2="1" y2="1">
        <stop offset="0" stop-color="#f2f6fb"/>
        <stop offset=".45" stop-color="#c9d9ec"/>
        <stop offset=".7" stop-color="#d6b9a6"/>
        <stop offset="1" stop-color="#a9c3e3"/>
      </linearGradient>
    </defs>
    <rect x="0" y="0" width="800" height="560" fill="url(#photoTone)" role="img" aria-label="Photo of a physiotherapist adjusting a knee brace on a patient's leg"/>
    <circle cx="83" cy="118" r="50" fill="#d9a93a" role="img" aria-label="Award badge"/>
    <polygon points="0,316 399,532 800,316 800,928 0,928" fill="var(--blue)"/>
    <polygon points="0,350 399,532 800,316 800,928 0,928" fill="#6a93cc" opacity=".55"/>
    <polygon points="0,312 399,516 800,312 800,318 399,532 0,318" fill="var(--green)"/>
  </svg>
  <div class="fold"></div>

  <h3 class="panel-heading services-title">Our services</h3>
  <p class="panel-text services-intro">We provide integrated assessment and care from interprofessional team of regulated healthcare professionals with proven experience in injury rehabilitation:</p>
  <ul class="service-list">
    <li>Physiatrists</li>
    <li>Sport medicine physicians</li>
    <li>Physiotherapists</li>
    <li>Chiropractors</li>
    <li>Massage therapists</li>
    <li>Acupuncturists</li>
    <li>Psychologists</li>
  </ul>
  <p class="panel-text services-extra">We provide custom medical bracing, orthotics, orthopedic shoes, assistive devices, and medical stockings, all in one place.</p>

  <h3 class="panel-heading registered-title">Only registered<br>physiotherapists</h3>
  <p class="panel-text registered-text">We strongly believe in consistency with your treatment plan. This means that you spend your time here one-on-one with your physiotherapist, not any students or assistants. You get consistent high quality care from a professional.</p>
  <h3 class="panel-heading attention-title">One-on-one attention</h3>
  <p class="panel-text attention-text">We book maximum 3 people per hour to ensure everyone gets adequate one-on-one time with their physiotherapist. This compares favorably with other clinics, who may book upwards of 5-6 per hour. The atmosphere is professional - balanced with friendly, caring and relaxed. Our highly qualified staff operate this way to help make your recovery faster and more enjoyable.</p>

</div>
</body>
</html>
```